design a construction company business card

Design business card around our logo. Card must have all the typical info: name, title, address, phone, email, business name, etc. Somewhere on the card I would like to see our motto "Built on integrity... Inspired by commitment." Consider adding a splash of bright orange to the card to complement the blues and silvers/grays in the logo. We are open to metallic inks, textures, etc. We would like to see options on both light and dark backgrounds. The font in the logo is Euro Technic Extended Regular.

```html
<!DOCTYPE html>
<html lang="en">
<head>
<meta charset="utf-8">
<title>Halden Contracting – Business Card</title>
<link href="https://fonts.googleapis.com/css2?family=Michroma&family=Montserrat:ital,wght@0,300;0,400;0,800;1,800&display=swap" rel="stylesheet">
<style>
  :root {
    --bg: #1c1c1e;
    --card-light: #ffffff;
    --card-dark: #26272a;
    --brand-blue: #2f6fd6;
    --name-blue: #2f86d8;
    --silver: #c9cbce;
    --text-light: #e6e7e9;
    --text-muted: #9a9da2;
    --motto-gray: #8a8c90;
  }
  * { margin: 0; padding: 0; box-sizing: border-box; }
  html, body { width: 1200px; height: 960px; overflow: hidden; }
  body {
    background: var(--bg);
    display: flex;
    flex-direction: column;
    align-items: center;
    justify-content: center;
    gap: 40px;
    font-family: "Montserrat", sans-serif;
  }
  .card {
    width: 700px;
    height: 400px;
    position: relative;
    border-radius: 4px;
    overflow: hidden;
  }

  /* Front: light */
  .card--front {
    background: var(--card-light);
    display: flex;
    flex-direction: column;
    align-items: center;
    justify-content: center;
    gap: 26px;
  }
  .brand-name {
    font-family: "Michroma", sans-serif;
    font-size: 34px;
    color: var(--brand-blue);
    letter-spacing: 2px;
    text-align: center;
    line-height: 1.3;
  }
  .brand-name small {
    display: block;
    font-size: 15px;
    letter-spacing: 5px;
  }
  .motto {
    font-family: "Montserrat", sans-serif;
    font-weight: 400;
    font-size: 14px;
    color: var(--motto-gray);
    letter-spacing: 0.5px;
  }

  /* Back: dark */
  .card--back {
    background: linear-gradient(160deg, #2e2f33 0%, var(--card-dark) 55%, #1f2022 100%);
  }
  .identity {
    position: absolute;
    top: 140px;
    right: 376px;
    text-align: right;
  }
  .person-name {
    font-weight: 800;
    font-style: italic;
    font-size: 22px;
    letter-spacing: 1.5px;
    color: var(--name-blue);
  }
  .person-title {
    font-weight: 300;
    font-size: 14px;
    color: var(--text-light);
    margin-top: 2px;
  }
  .divider {
    position: absolute;
    left: 346px;
    top: 132px;
    width: 1px;
    height: 72px;
    background: var(--text-muted);
  }
  .contact-list {
    position: absolute;
    left: 368px;
    top: 130px;
    list-style: none;
  }
  .contact-list li {
    display: flex;
    align-items: center;
    gap: 12px;
    font-weight: 300;
    font-size: 14px;
    color: var(--text-light);
    line-height: 26px;
  }
  .contact-list svg { width: 14px; height: 14px; fill: var(--name-blue); }
  .address {
    position: absolute;
    left: 240px;
    bottom: 52px;
    font-weight: 300;
    font-size: 14px;
    color: var(--text-light);
  }
  .base-line {
    position: absolute;
    left: 40px;
    right: 0;
    bottom: 36px;
    height: 2px;
    background: linear-gradient(90deg, var(--text-muted), var(--silver) 60%, #ffffff);
  }
</style>
</head>
<body>

  <section class="card card--front">
    <div class="brand-name">HALDEN<small>CONTRACTING, INC.</small></div>
    <p class="motto">Built on integrity... Inspired by commitment</p>
  </section>

  <section class="card card--back">
    <div class="identity">
      <div class="person-name">YOUR NAME</div>
      <div class="person-title">Your Title</div>
    </div>
    <div class="divider"></div>
    <ul class="contact-list">
      <li>
        <svg viewBox="0 0 24 24" aria-hidden="true"><path d="M6.6 10.8a15.1 15.1 0 0 0 6.6 6.6l2.2-2.2a1 1 0 0 1 1-.25 11.4 11.4 0 0 0 3.6.57 1 1 0 0 1 1 1V20a1 1 0 0 1-1 1A17 17 0 0 1 3 4a1 1 0 0 1 1-1h3.5a1 1 0 0 1 1 1c0 1.25.2 2.45.57 3.57a1 1 0 0 1-.25 1z"/></svg>
        123-456-2100
      </li>
      <li>
        <svg viewBox="0 0 24 24" aria-hidden="true"><path d="M2 5h20v14H2z M2 5l10 7 10-7" /></svg>
        youremail@mailbox.com
      </li>
      <li>
        <svg viewBox="0 0 24 24" aria-hidden="true"><circle cx="12" cy="12" r="10"/></svg>
        www.yourwebsite.com
      </li>
    </ul>
    <p class="address">Your address, city, state, ZIP 0000</p>
    <div class="base-line"></div>
  </section>

</body>
</html>
```